Solution Matrix for our Company

Develop an image that describes our "4 solutions". We eventually will list the products and services we have that address the solution being discussed. Our main website is http://brightlanework.com/. Feel free to look through the material there as well as the material we are addressing.

The mock document is a summary of the 4 solution buckets. We have also attached some samples from states that have done similar work. Feel free to be creative and use graphics and/or pictures in your design

Target Market(s)

Education

```html
<!DOCTYPE html>
<html lang="en">
<head>
<meta charset="utf-8">
<title>Brightlane Work – Solution Matrix</title>
<link rel="stylesheet" href="https://fonts.googleapis.com/css2?family=Roboto:wght@400;500;700&display=swap">
<style>
  :root {
    --canvas: #e8dccb;
    --header-band: #e5d4be;
    --footer-band: #fdeeda;
    --box-fill: #f6e8d8;
    --box-line: #9a948c;
    --ink: #4a4a4a;
    --accent: #f7941d;
    --art-a: #9fd3e0;
    --art-b: #f3a24a;
  }
  * { box-sizing: border-box; margin: 0; padding: 0; }
  html, body { width: 1200px; height: 1008px; overflow: hidden; }
  body {
    position: relative;
    background: var(--canvas);
    font-family: "Roboto", Arial, sans-serif;
    color: var(--ink);
  }
  .header-band {
    position: absolute; left: 154px; top: 59px; width: 887px; height: 136px;
    background: var(--header-band);
  }
  .brand-mark {
    position: absolute; left: 10px; top: 50px;
    display: flex; align-items: center; gap: 6px;
    font-size: 26px; font-weight: 700; line-height: 30px; color: var(--accent);
    white-space: nowrap;
  }
  .brand-mark .square { width: 12px; height: 12px; background: var(--ink); flex: none; }
  .header-intro {
    position: absolute; left: 185px; top: 50px; width: 670px;
    font-size: 15px; line-height: 18px; color: var(--accent);
  }
  .hero-art {
    position: absolute; left: 369px; top: 217px; width: 405px; height: 514px;
    border-radius: 40% 40% 20% 20%;
    background: radial-gradient(ellipse at 50% 45%, var(--art-a) 0%, rgba(159,211,224,0.55) 35%, rgba(243,162,74,0.25) 60%, rgba(232,220,203,0) 75%);
  }
  .solution-box {
    position: absolute; width: 250px;
    background: var(--box-fill); border: 1px solid var(--box-line);
    padding: 6px 2px 4px 5px;
    font-size: 15px; line-height: 18px; letter-spacing: -0.1px;
    overflow: hidden;
  }
  .solution-box h2 { font-size: 15px; font-weight: 700; line-height: 20px; }
  .solution-box ul { list-style: none; color: var(--accent); }
  .solution-box li { position: relative; padding: 2px 0 0 22px; line-height: 18px; white-space: nowrap; }
  .solution-box li::before { content: "•"; position: absolute; left: 0; font-size: 11px; }
  .solution-box li.wrap { padding-left: 0; text-indent: 22px; white-space: normal; }
  .solution-box li.wrap::before { text-indent: 0; }
  .box-supported { left: 162px; top: 297px; height: 189px; }
  .box-prepared  { left: 783px; top: 299px; width: 256px; height: 193px; padding-left: 6px; }
  .box-engaged   { left: 161px; top: 679px; height: 191px; }
  .box-wise      { left: 789px; top: 682px; height: 190px; padding-left: 7px; }
  .callouts { position: absolute; left: 0; top: 0; width: 1200px; height: 1008px; pointer-events: none; }
  .footer-band {
    position: absolute; left: 0; top: 942px; width: 1200px; height: 66px;
    background: var(--footer-band);
  }
  .footer-brand { position: absolute; left: 860px; top: 20px; width: 180px; text-align: right; }
  .footer-brand .name { font-size: 15px; font-weight: 700; color: var(--accent); line-height: 16px; }
  .footer-brand .tagline { font-size: 7.5px; letter-spacing: 0.6px; color: var(--ink); }
</style>
</head>
<body>
  <header class="header-band">
    <div class="brand-mark"><span class="square"></span>Brightlane</div>
    <p class="header-intro">Brightlane Work relies on robust labor market data tools and sound educational research to guide our development efforts and encourage the use of informed career readiness practices educational settings.</p>
  </header>

  <div class="hero-art" role="img" aria-label="Illustration of a student in light armour holding a book and a scroll, standing on a sketched forest path"></div>

  <svg class="callouts" viewBox="0 0 1200 1008" aria-hidden="true">
    <g fill="#f6e8d8" stroke="none">
      <polygon points="346,485 357,485 433,510"/>
      <polygon points="794,491 843,491 767,517"/>
      <polygon points="253,680 337,680 372,644"/>
      <polygon points="845,683 947,683 829,646"/>
    </g>
    <g fill="none" stroke="#9a948c" stroke-width="0.8">
      <polyline points="346,486 433,510 357,486"/>
      <polyline points="794,492 767,517 843,492"/>
      <polyline points="253,679 372,644 337,679"/>
      <polyline points="845,682 829,646 947,682"/>
    </g>
  </svg>

  <section class="solution-box box-supported">
    <h2>Career Supported</h2>
    <p>Students benefit from informed edu&shy;cational leadership and policymak&shy;ing that result in effective career re&shy;sources and learning opportunities.</p>
    <ul>
      <li>Brightlane Policy Tools</li>
      <li>Perkins V Technical Support</li>
      <li>Professional Development</li>
      <li>Industry-Education Relationships</li>
    </ul>
  </section>

  <section class="solution-box box-prepared">
    <h2>Career Prepared</h2>
    <p>Students have the necessary foun&shy;dational, technical, and workplace skills needed to support success in a variety of careers.</p>
    <ul>
      <li>Career-Focused Curricula</li>
      <li class="wrap">Math Assessments with Numera Career Database (powered by the Numera® Framework for Mathe&shy;matics)</li>
    </ul>
  </section>

  <section class="solution-box box-engaged">
    <h2>Career Engaged</h2>
    <p>Students are motivated and inspired to develop career skills and seek employment opportunities that meet both personal and community<br>needs.</p>
    <ul>
      <li>Career Awareness &amp; Exposure</li>
      <li class="wrap">Purposeful Learning Connected to Careers</li>
    </ul>
  </section>

  <section class="solution-box box-wise">
    <h2>Career Wise</h2>
    <p>Students have insight into personal values and interests, as well as the economic realities of the job market, that supports informed career deci&shy;sions</p>
    <ul>
      <li>Career Pathways</li>
      <li>Career Exploration</li>
      <li>Educator Career Guides</li>
    </ul>
  </section>

  <footer class="footer-band">
    <div class="footer-brand">
      <div class="name">BRIGHTLANE WORK</div>
      <div class="tagline">Education with Destination</div>
    </div>
  </footer>
</body>
</html>
```